Automotive eCommerce Business looking for a business card design

Looking for a clean and simple business card design. Our company name is "Brindle Auto" and we are a company specializing in the ecommerce sales of automotive parts, specifically for pick up trucks and large SUVs. Our company colours are red, black, and white.

Feel free to use the logo provided or create a new logo that you seem fit. Looking forward to your creative ideas!

Industry/Entity Type

Automotive

Contact Information for Business Card

We were thinking of a possibly two-sided design featuring just the logo and company name on one side, and personal information on the other side. Single sided designs will be considered as well.

Font styles to use
Serif
Sans Serif
Decorative

Colors
ec1f27
ffffff
000000

Requirements
Must have
• Space for employee's name, title, phone number and email address, along with the company address and website somewhere.

```html
<!DOCTYPE html>
<html lang="en">
<head>
<meta charset="utf-8">
<title>Brindle Auto Ltd. – Business Card</title>
<link rel="stylesheet" href="https://fonts.googleapis.com/css2?family=Cinzel:wght@400&family=Roboto:wght@400;500&family=Roboto+Condensed:wght@500&display=swap">
<style>
  :root {
    --backdrop: #e7e4df;
    --card: #f4f4f3;
    --brand-red: #a31f24;
    --ink: #555555;
    --ink-soft: #5c5c5c;
    --white: #ffffff;
  }
  * { margin: 0; padding: 0; box-sizing: border-box; }
  html, body { width: 1200px; height: 960px; overflow: hidden; }
  body { background: var(--backdrop); position: relative; font-family: "Roboto", Arial, sans-serif; }

  .card {
    position: absolute;
    left: 320px;
    width: 600px;
    background: var(--card);
    border-radius: 22px;
    box-shadow: 0 2px 6px rgba(0,0,0,0.18);
    overflow: hidden;
  }

  /* Front */
  .card--front { top: 95px; height: 355px; }
  .brand-mark {
    position: absolute;
    left: 228px; top: 78px;
    width: 145px; height: 145px;
    background: var(--brand-red);
  }
  .brand-name {
    position: absolute;
    left: 0; right: 0; top: 242px;
    text-align: center;
    font-family: "Cinzel", Georgia, serif;
    font-size: 27px;
    color: var(--ink);
    letter-spacing: 0.5px;
  }
  .brand-web {
    position: absolute;
    left: 0; right: 0; top: 303px;
    text-align: center;
    font-size: 15px;
    letter-spacing: 5px;
    color: var(--ink);
  }

  /* Back */
  .card--back { top: 493px; height: 342px; }
  .name-band {
    position: absolute;
    left: 300px; top: 29px;
    width: 300px; height: 118px;
    background: var(--brand-red);
  }
  .band-square {
    position: absolute;
    left: 272px; top: 31px;
    width: 114px; height: 114px;
    background: var(--brand-red);
    border: 3px solid var(--white);
  }
  .person {
    position: absolute;
    right: 30px; top: 66px;
    text-align: right;
    color: var(--white);
  }
  .person__name {
    font-family: "Roboto Condensed", Arial, sans-serif;
    font-weight: 500;
    font-size: 21px;
    line-height: 24px;
  }
  .person__title { font-size: 14px; font-weight: 500; line-height: 20px; margin-top: 1px; }

  .address {
    position: absolute;
    left: 34px; top: 170px;
    font-size: 14px; line-height: 18px;
    color: var(--ink-soft);
  }
  .contacts {
    position: absolute;
    left: 34px; top: 217px;
    list-style: none;
    font-size: 14px; line-height: 19.3px;
    color: var(--ink-soft);
  }
  .contacts li { display: flex; align-items: center; }
  .contacts svg { width: 13px; height: 13px; margin-right: 10px; fill: var(--brand-red); flex: none; }
</style>
</head>
<body>
  <section class="card card--front" aria-label="Card front">
    <div class="brand-mark"></div>
    <h1 class="brand-name">Brindle Auto Ltd.</h1>
    <p class="brand-web">www.brindleauto.com</p>
  </section>

  <section class="card card--back" aria-label="Card back">
    <div class="name-band"></div>
    <div class="band-square"></div>
    <div class="person">
      <p class="person__name">OWEN HARTLEY</p>
      <p class="person__title">CEO/FOUNDER</p>
    </div>

    <address class="address" style="font-style:normal">
      412 Cedar Ridge Road<br>
      Juneau, Alaska 34518
    </address>

    <ul class="contacts">
      <li><svg viewBox="0 0 16 16" aria-hidden="true"><path d="M3.6 1.2l2.3 2.6-1.3 2c.9 2 2.5 3.6 4.5 4.5l2-1.3 2.6 2.3-1.3 2.2C7 13.3 2.7 9 1.4 2.5z"/></svg>555 214 3087</li>
      <li><svg viewBox="0 0 16 16" aria-hidden="true"><path d="M4 0h8v16H4zM5.5 2v10h5V2zM7 13.2h2v1.4H7z" fill-rule="evenodd"/></svg>555 730 1642</li>
      <li><svg viewBox="0 0 16 16" aria-hidden="true"><path d="M4 1h8v4H4zM1 6h14v6h-3v3H4v-3H1zM5.5 10v3.5h5V10z" fill-rule="evenodd"/></svg>555 902 4415</li>
      <li><svg viewBox="0 0 16 16" aria-hidden="true"><path d="M1 3h14v1L8 9 1 4zM1 5.5l7 5 7-5V13H1z"/></svg>owen@brindleauto.com</li>
      <li><svg viewBox="0 0 16 16" aria-hidden="true"><circle cx="8" cy="8" r="7"/><path d="M4 5c2 0 2 2 3 3s-1 3 0 4M10 3c0 2 2 2 3 3" stroke="#f4f4f3" stroke-width="1.3" fill="none"/></svg>www.brindleparts.com</li>
    </ul>
  </section>
</body>
</html>
```